KRV Business Card

Looking for a business card for my restaurant group I own. Four different concepts:

Copperfield Alehouse
Bristow Alehouse
Tanager's Stone Hearth Kitchen
Pellston Patty Company

Card doesn't need to include all the logos.

```html
<!DOCTYPE html>
<html lang="en">
<head>
<meta charset="utf-8">
<title>KRV Business Card</title>
<link href="https://fonts.googleapis.com/css2?family=Poppins:wght@400;500;600&display=swap" rel="stylesheet">
<style>
  :root {
    --backdrop: #242222;
    --card-white: #ffffff;
    --gold: #cfab6b;
    --slate: #6f6f72;
    --slate-pattern: #77777a;
    --ink: #4a4a4c;
    --soft-ink: #6a6a6a;
  }
  * { box-sizing: border-box; margin: 0; padding: 0; }
  html, body {
    width: 1125px; height: 1200px; overflow: hidden;
    background: var(--backdrop);
    font-family: "Poppins", sans-serif;
  }
  .card {
    position: absolute; left: 171px; width: 826px; height: 472px;
    overflow: hidden;
  }
  .card-front { top: 106px; background: var(--card-white); }
  .card-back { top: 639px; background: var(--slate); }

  .brand-block {
    position: absolute; left: 40px; width: 346px; top: 150px;
    display: flex; flex-direction: column; align-items: center; gap: 14px;
  }
  .brand-square { width: 22px; height: 22px; background: var(--gold); }
  .brand-name {
    color: var(--gold); font-weight: 500; text-align: center;
    font-size: 30px; line-height: 1.2; letter-spacing: 3px; text-transform: uppercase;
  }

  .divider {
    position: absolute; left: 390px; top: 95px; width: 3px; height: 248px;
    background: linear-gradient(to bottom, rgba(110,110,110,0), #8a8a8a 20%, #8a8a8a 80%, rgba(110,110,110,0));
  }

  .contact { position: absolute; left: 425px; top: 92px; color: var(--ink); }
  .person-name { color: var(--gold); font-weight: 600; font-size: 30px; line-height: 38px; }
  .person-title { color: var(--soft-ink); font-size: 20px; line-height: 24px; }
  .address { margin-top: 12px; font-size: 19.5px; line-height: 25px; }
  .lines { margin-top: 9px; list-style: none; }
  .lines li {
    display: flex; align-items: center; gap: 12px;
    font-size: 19.5px; line-height: 26px;
  }
  .lines svg { width: 18px; height: 18px; flex: none; fill: var(--gold); }

  .web-band {
    position: absolute; left: 28px; top: 419px; width: 771px; height: 33px;
    background: var(--gold);
    clip-path: polygon(0 0, 96% 0, 100% 100%, 4% 100%);
    color: #fff; font-size: 19px; letter-spacing: 4.6px;
    display: flex; align-items: center; justify-content: center;
  }
  .base-strip {
    position: absolute; left: 0; bottom: 0; width: 100%; height: 20px;
    background: var(--slate);
  }

  .back-texture {
    position: absolute; inset: 0;
    background: linear-gradient(135deg, var(--slate-pattern), var(--slate));
  }
  .back-mark {
    position: absolute; right: 68px; top: 322px;
    color: #fff; font-weight: 600; font-size: 50px; letter-spacing: 2px; line-height: 1;
  }
</style>
</head>
<body>

<section class="card card-front">
  <div class="brand-block">
    <span class="brand-square"></span>
    <div class="brand-name">Kestrel Ridge<br>Ventures</div>
  </div>

  <div class="divider"></div>

  <div class="contact">
    <h1 class="person-name">Daniel Hartley</h1>
    <p class="person-title">President</p>
    <p class="address">4120 Alder Court<br>Juneau, Alaska 99801</p>
    <ul class="lines">
      <li>
        <svg viewBox="0 0 24 24" aria-hidden="true"><path d="M6.6 10.8a15.1 15.1 0 0 0 6.6 6.6l2.2-2.2c.3-.3.7-.4 1-.2 1.1.4 2.3.6 3.6.6.6 0 1 .4 1 1V20c0 .6-.4 1-1 1A17 17 0 0 1 3 4c0-.6.4-1 1-1h3.5c.6 0 1 .4 1 1 0 1.3.2 2.5.6 3.6.1.3 0 .7-.2 1z"/></svg>
        555-214-7730
      </li>
      <li>
        <svg viewBox="0 0 24 24" aria-hidden="true"><path d="M7 1h10a2 2 0 0 1 2 2v18a2 2 0 0 1-2 2H7a2 2 0 0 1-2-2V3a2 2 0 0 1 2-2zm0 3v15h10V4z"/></svg>
        555-608-3192
      </li>
      <li>
        <svg viewBox="0 0 24 24" aria-hidden="true"><path d="M7 2h10v5H7zM4 8h16a2 2 0 0 1 2 2v8h-4v4H6v-4H2v-8a2 2 0 0 1 2-2zm4 8v4h8v-4z"/></svg>
        555-431-2046
      </li>
      <li>
        <svg viewBox="0 0 24 24" aria-hidden="true"><path d="M2 5h20v14H2zm2 2v.5l8 5 8-5V7zm0 2.8V17h16V9.8l-8 5z"/></svg>
        name@kestrelridgeventures.com
      </li>
    </ul>
  </div>

  <div class="web-band">www.kestrelridgeventures.com</div>
  <div class="base-strip"></div>
</section>

<section class="card card-back">
  <div class="back-texture" role="img" aria-label="Repeating tonal brand pattern across the card back"></div>
  <div class="back-mark">KRV</div>
</section>

</body>
</html>
```